Beacon Advisory Website

I currently have a website www.beaconadvisoryinc.com. We are a IT Consulting Company. Our website will pretty much tell out our services. I am looking to enhance my website and make it look more professional. Looking for very classy and Contemporary look and design for my website.

It Company

```html
<!DOCTYPE html>
<html lang="en">
<head>
<meta charset="utf-8">
<title>Beacon Advisory</title>
<link href="https://fonts.googleapis.com/css2?family=Source+Sans+3:wght@300;400;600;700&display=swap" rel="stylesheet">
<style>
:root{
  --navy:#0d3f7c;
  --royal:#1a5ea8;
  --sky:#0e8fd6;
  --accent:#1a8fd0;
  --ink:#2b2b2b;
  --muted:#6e6e6e;
  --soft:#f5f5f5;
  --white:#ffffff;
  --rule:#1a6fb8;
}
*{box-sizing:border-box;margin:0;padding:0}
html,body{width:1200px;height:2571px;overflow:hidden}
body{font-family:"Source Sans 3",sans-serif;color:var(--ink);background:var(--white);position:relative}
.abs{position:absolute}

/* header */
.site-header{position:absolute;left:0;top:0;width:1200px;height:99px;background:var(--white)}
.header-swoosh{position:absolute;left:0;top:0}
.brand{position:absolute;display:flex;align-items:center;gap:10px}
.brand-mark{width:34px;height:34px;background:var(--royal);border-radius:4px}
.brand-name{font-weight:700;font-size:24px;color:var(--navy);letter-spacing:.5px}
.main-nav{position:absolute;left:412px;top:57px;display:flex;gap:0}
.main-nav a{font-size:14px;font-weight:600;color:var(--ink);text-decoration:none;letter-spacing:.3px}
.main-nav a+a{margin-left:51px}

/* hero */
.hero{position:absolute;left:0;top:99px;width:1200px;height:498px;
  background:linear-gradient(100deg,#1a7fd4 0%,#1566bf 40%,#0d3d8a 75%,#0a2c6a 100%)}
.hero-title{position:absolute;left:127px;top:203px;font-size:37px;font-weight:600;color:var(--white);letter-spacing:.5px}
.hero-text{position:absolute;left:130px;top:256px;width:400px;font-size:13.5px;line-height:23px;color:#d6e6f7;font-weight:300}
.btn-dark{position:absolute;left:131px;top:347px;width:138px;height:40px;background:#0f3c7a;color:var(--white);font-size:13px;font-weight:600;display:flex;align-items:center;justify-content:center;letter-spacing:.3px}
.dots{position:absolute;display:flex;gap:8px}
.dots span{width:9px;height:9px;border-radius:50%;background:#cfd8e3}
.hero .dots span{background:var(--white)}
.hero .dots span:first-child{background:#7fb3e6}

/* welcome */
.welcome{position:absolute;left:0;top:597px;width:1200px;height:339px;background:var(--soft);text-align:center}
.section-title{font-size:23px;font-weight:600;letter-spacing:.3px}
.welcome .section-title{position:absolute;left:0;right:0;top:57px;color:var(--accent)}
.welcome-text{position:absolute;left:160px;width:880px;top:132px;font-size:13.5px;line-height:24px;color:#555}
.btn-outline{position:absolute;left:530px;top:267px;width:111px;height:37px;border:1px solid #8a8a8a;font-size:12.5px;font-weight:600;color:var(--navy);display:flex;align-items:center;justify-content:center;background:var(--white)}

/* services */
.services{position:absolute;left:0;top:936px;width:1200px;height:441px;background:var(--white)}
.services .section-title{position:absolute;left:0;right:0;top:63px;text-align:center;color:var(--navy)}
.service{position:absolute;top:158px;width:288px}
.service-head{display:flex;align-items:center;gap:14px;height:60px;border-bottom:2px solid var(--rule);padding-bottom:8px}
.service-icon{width:58px;height:58px;border-radius:50%;background:var(--accent);display:flex;align-items:center;justify-content:center;flex:none}
.service-name{font-size:19px;color:#333;letter-spacing:.3px}
.service-text{margin-top:24px;font-size:11.5px;line-height:20px;color:#444}
.services .dots{left:552px;top:400px}
.services .dots span:first-child{background:var(--accent)}

/* feature bands */
.band{position:absolute;left:0;width:1200px}
.band-it{top:1377px;height:354px;background:var(--royal);color:var(--white)}
.band-staff{top:1731px;height:353px;background:var(--white)}
.band-offshore{top:2084px;height:353px;background:var(--sky);color:var(--white)}
.photo-circle{position:absolute;border-radius:50%;border:5px solid var(--white);box-shadow:0 4px 10px rgba(0,0,0,.25)}
.band-title{position:absolute;font-size:22px;font-weight:600;letter-spacing:.4px}
.band-text{position:absolute;font-size:13.5px;line-height:24px}
.band-it .band-text,.band-offshore .band-text{color:#e3eefa}
.band-staff .band-title{color:var(--navy)}
.band-staff .band-text{color:#666}

/* footer */
.site-footer{position:absolute;left:0;top:2437px;width:1200px;height:134px;background:var(--white)}
.footer-nav{position:absolute;left:417px;top:51px;display:flex;align-items:center;font-size:14px;font-weight:600;color:#333}
.footer-nav .sep{margin:0 22px;font-weight:400}
.copyright{position:absolute;left:760px;top:84px;font-size:13px;font-weight:600;color:#333}
</style>
</head>
<body>

<header class="site-header">
  <svg class="header-swoosh" width="1200" height="99" viewBox="0 0 1200 99" aria-hidden="true">
    <path d="M345 0 C325 30 330 70 380 86 L1200 86 L1200 82 L390 82 C355 70 350 30 370 0 Z" fill="#1a6fb8"/>
    <path d="M370 0 C352 28 360 62 395 76 L1200 76 L1200 74 L398 74 C366 60 362 30 380 0 Z" fill="#0e8fd6"/>
  </svg>
  <div class="brand" style="left:117px;top:28px">
    <span class="brand-mark"></span>
    <span class="brand-name">BEACON ADVISORY</span>
  </div>
  <nav class="main-nav">
    <a href="#">COMPANY</a><a href="#">SERVICES</a><a href="#">SOLUTIONS</a><a href="#">RESOURCES</a><a href="#">CAREER</a><a href="#">CONTACT US</a>
  </nav>
</header>

<section class="hero" role="img" aria-label="Business person touching glowing blue gear wheels">
  <h1 class="hero-title">BEACON ADVISORY</h1>
  <p class="hero-text">Sed ut perspiciatis unde omnis iste natus error sit voluptatem accusantium doloremque laudantium, totam rem aperiam, eaque ipsa quae ab illo inventore veritatis et quasi architecto</p>
  <div class="btn-dark">LEARN MORE</div>
  <div class="dots" style="left:555px;top:459px"><span></span><span></span><span></span><span></span></div>
</section>

<section class="welcome">
  <h2 class="section-title">WELCOME TO BEACON ADVISORY</h2>
  <p class="welcome-text">Today's IT market is a dynamic, fast-paced industry, with ever-increasing demands. Meeting these demands for over 25 years, Beacon Advisory maintains a global presence, aggressively recruiting expertly qualified IT and Management Professionals from around the world and cultivating key partnerships with corporations to understand their business models end-to-end, with a goal of delivering exceptional client service and ensuring a consistent delivery of the talent needed to drive results</p>
  <div class="btn-outline">LEARN MORE</div>
</section>

<section class="services">
  <h2 class="section-title">OUR SERVICES</h2>

  <div class="service" style="left:129px">
    <div class="service-head">
      <span class="service-icon">
        <svg width="28" height="24" viewBox="0 0 28 24" aria-hidden="true"><g fill="#fff"><rect x="1" y="17" width="4" height="6"/><rect x="7" y="13" width="4" height="10"/><rect x="13" y="9" width="4" height="14"/><rect x="19" y="5" width="4" height="18"/><rect x="25" y="1" width="3" height="22"/></g></svg>
      </span>
      <span class="service-name">BUSINESS</span>
    </div>
    <p class="service-text">Lorem Ipsum is simply dummy text of the printing and typesetting industry. Lorem Ipsum has been the industry's standard dummy text ever since the 1500s, when an unknown printer took a galley of type and scrambled it to make a type specimen book.</p>
  </div>

  <div class="service" style="left:439px">
    <div class="service-head">
      <span class="service-icon">
        <svg width="22" height="30" viewBox="0 0 22 30" aria-hidden="true"><path d="M11 2a9 9 0 0 0-5 16.5V22h10v-3.5A9 9 0 0 0 11 2z" fill="none" stroke="#fff" stroke-width="2.4"/><rect x="6" y="24" width="10" height="2.4" fill="#fff"/><rect x="8" y="27.5" width="6" height="2" fill="#fff"/></svg>
      </span>
      <span class="service-name">TECHNOLOGY</span>
    </div>
    <p class="service-text">Lorem Ipsum is simply dummy text of the printing and typesetting industry. Lorem Ipsum has been the industry's standard dummy text ever since the 1500s, when an unknown printer took a galley of type and scrambled it to make a type specimen book.</p>
  </div>

  <div class="service" style="left:753px">
    <div class="service-head">
      <span class="service-icon">
        <svg width="28" height="28" viewBox="0 0 28 28" aria-hidden="true"><path d="M20 4H5a2 2 0 0 0-2 2v17a2 2 0 0 0 2 2h17a2 2 0 0 0 2-2V10" fill="none" stroke="#fff" stroke-width="2.4"/><path d="M22 2l4 4-12 12-5 1 1-5z" fill="#fff"/></svg>
      </span>
      <span class="service-name">APPLICATION</span>
    </div>
    <p class="service-text">Lorem Ipsum is simply dummy text of the printing and typesetting industry. Lorem Ipsum has been the industry's standard dummy text ever since the 1500s, when an unknown printer took a galley of type and scrambled it to make a type specimen book.</p>
  </div>

  <div class="dots"><span></span><span></span><span></span><span></span></div>
</section>

<section class="band band-it">
  <div class="photo-circle" role="img" aria-label="Team working together at laptops in a bright office" style="left:129px;top:25px;width:308px;height:308px;background:linear-gradient(160deg,#dfe7ee,#9fb3c4 55%,#5b6b78)"></div>
  <h2 class="band-title" style="left:519px;top:47px">IT CONSULTING</h2>
  <p class="band-text" style="left:520px;top:110px;width:520px">Information technology should improve business results. Crestline helps companies make sure it does. We look at IT issues strategically, in the broader context of our clients' business. Our experts provide an objective, independent perspective to help companies realize the full potential of their IT resources, investments and assets.</p>
  <p class="band-text" style="left:520px;top:230px;width:520px">We draw on global experience across industries and technologies to help solve companies' most complex IT challenges. More than 40% of our work is done in the context of major transformation in the business or in IT.</p>
</section>

<section class="band band-staff">
  <h2 class="band-title" style="left:128px;top:60px">STAFF AUGMENTATION</h2>
  <p class="band-text" style="left:129px;top:122px;width:520px">For years Beacon Advisory has been offering our customers the ability to augment their existing staff with temporary highly skilled IT professionals who can help address immediate short term needs. We know that often our customers have brief spikes in their need for reporting, for example. With internal IT teams focused on more strategic projects, it can be difficult to justify diverting a team member for a few weeks to relieve this short term pressure from business users. This is an ideal situation in which to consider bringing in one of our team.</p>
  <div class="photo-circle" role="img" aria-label="Silhouetted business team standing before tall glass towers" style="left:740px;top:26px;width:302px;height:302px;background:linear-gradient(180deg,#cfe1f2,#8fb0d0 50%,#2c3e55)"></div>
</section>

<section class="band band-offshore">
  <div class="photo-circle" role="img" aria-label="Businessman reviewing documents at a desk" style="left:129px;top:23px;width:308px;height:308px;background:linear-gradient(160deg,#f2f2f0,#c9c4bb 55%,#6e6a64)"></div>
  <h2 class="band-title" style="left:520px;top:94px">OFFSHORE</h2>
  <p class="band-text" style="left:520px;top:155px;width:520px">Our Offshore development model has a unique distinction of providing efficient software solutions with cost and quality advantage, using state-of-the-art technologies, having the capacity to handle large projects and, above all, the ability to execute timely deliveries.</p>
</section>

<footer class="site-footer">
  <svg class="abs" style="left:0;top:0" width="1200" height="134" viewBox="0 0 1200 134" aria-hidden="true">
    <path d="M130 8 L1080 8 C1110 8 1125 40 1140 134 L1150 134 C1138 36 1120 2 1080 2 L130 2 Z" fill="#1a6fb8"/>
    <path d="M1090 14 C1120 20 1138 60 1152 134 L1160 134 C1148 60 1130 16 1095 10 Z" fill="#0e8fd6"/>
  </svg>
  <div class="brand" style="left:146px;top:52px">
    <span class="brand-mark"></span>
    <span class="brand-name">BEACON ADVISORY</span>
  </div>
  <nav class="footer-nav">
    <span>COMPANY</span><span class="sep">|</span><span>SERVICES</span><span class="sep">|</span><span>SOLUTIONS</span><span class="sep">|</span><span>RESOURCES</span><span class="sep">|</span><span>CAREER</span><span class="sep">|</span><span>CONTACT US</span>
  </nav>
  <p class="copyright">© 2016 COMPANY NAME | ALL RIGHTS RESERVED</p>
</footer>

</body>
</html>
```